Smoker Oven Manufacturer Looking for Commercial Product Catalog

We are a small, family owned/operated international smoker oven manufacturer known for our end products and customer service. Our products include residential smokers, residential pellet grills, competition barbecue smokers, commercial smokers, commercial charbroilers, grilling and smoker accessories, sauces, spices, woods and food grade pellets. We have 6 international distributors and ship products everywhere.
Up until now, we have used individual spec sheets and a customized folder to send out information to prospects and we would like to move over to a catalog design.
We would like the final design to include red and our logo. The inside of the catalog is not as important to us as the cover, but we would like something that flows well. We like using food pictures as attention grabbers but also need balance so people who see our catalog do not think we are a restaurant. The end catalog will be about 20 pages.
Attached you will find examples of our spec sheets and the order we would like products in plus some of our current smoker images. For more information, please see our website: www.brindlekiln.com.
All of the product spec, past branding and content layout can be found in dropbox: https://www.fernvault.com/sh/qp4tzwlamr83hx2/KXTE7pQwdnrjVF3k1-hgyLs9b?dl=0
Updates

Target Market(s)

Owners/Operators/Chefs in the food industry

Industry/Entity Type

Commercial

Contact Information for Business Card

similar look and feel to the catalog

Colors
ec1f27
000000

Requirements
Must have
• Brindlekiln Logo, Red in the design but does not have to be the primary color used, products photos
Nice to have
• Food pictures

```html
<!DOCTYPE html>
<html lang="en">
<head>
<meta charset="utf-8">
<title>Brindlekiln Product Catalog Cover</title>
<link rel="stylesheet" href="https://fonts.googleapis.com/css2?family=Lato:wght@300;400&family=Montserrat:wght@600;800&display=swap">
<style>
  :root {
    --brand-red: #ec1f27;
    --ink: #1a1a1a;
    --page: #f3f3f3;
    --backdrop: #e6e3de;
    --soft-grey: #9a9a9a;
    --white: #ffffff;
  }
  html, body {
    margin: 0;
    width: 1200px;
    height: 804px;
    overflow: hidden;
    background: var(--backdrop);
  }
  .cover {
    position: absolute;
    left: 330px;
    top: 20px;
    width: 540px;
    height: 764px;
    background: var(--page);
    box-shadow: 0 2px 10px rgba(0,0,0,0.12);
    overflow: hidden;
  }
  .brand {
    position: absolute;
    left: 40px;
    top: 112px;
    display: flex;
    align-items: center;
    gap: 10px;
  }
  .brand-name {
    font-family: "Montserrat", sans-serif;
    font-weight: 800;
    font-size: 30px;
    letter-spacing: 0.5px;
    color: var(--ink);
  }
  .brand-mark {
    width: 22px;
    height: 22px;
    background: var(--brand-red);
  }
  .tagline {
    position: absolute;
    left: 318px;
    top: 72px;
    margin: 0;
    font-family: "Lato", sans-serif;
    font-weight: 300;
    font-size: 21px;
    line-height: 1.15;
    color: var(--soft-grey);
  }
  .intro {
    position: absolute;
    left: 40px;
    right: 40px;
    top: 206px;
    margin: 0;
    font-family: "Lato", sans-serif;
    font-size: 8px;
    line-height: 1.5;
    color: #555;
  }
  .hero-photo {
    position: absolute;
    left: 0;
    top: 244px;
    width: 540px;
    height: 210px;
    background: linear-gradient(120deg, #5a2a12 0%, #b5642c 30%, #d98c4a 50%, #a4521f 72%, #3b1a0c 100%);
  }
  .title-block {
    position: absolute;
    left: 0;
    top: 432px;
    width: 340px;
    height: 130px;
    background: var(--brand-red);
    color: var(--white);
    font-family: "Montserrat", sans-serif;
  }
  .title-kicker {
    position: absolute;
    left: 40px;
    top: 38px;
    margin: 0;
    font-weight: 600;
    font-size: 17px;
    letter-spacing: 0.5px;
  }
  .title-main {
    position: absolute;
    left: 38px;
    top: 56px;
    margin: 0;
    font-weight: 600;
    font-size: 44px;
    letter-spacing: 1px;
  }
  .product-frame {
    position: absolute;
    width: 150px;
    height: 122px;
    border: 3px solid var(--brand-red);
    background: var(--white);
    padding: 6px;
    box-sizing: border-box;
  }
  .product-frame.first { left: 350px; top: 336px; }
  .product-frame.second { left: 368px; top: 478px; }
  .product-shot {
    width: 100%;
    height: 100%;
    background: linear-gradient(160deg, #f2f2f2 0%, #c9c9c9 55%, #8e8e8e 100%);
  }
  .contact {
    position: absolute;
    left: 0;
    right: 0;
    top: 690px;
    margin: 0;
    text-align: center;
    font-family: "Lato", sans-serif;
    font-size: 13px;
    color: var(--ink);
  }
</style>
</head>
<body>
  <main class="cover">
    <div class="brand">
      <span class="brand-name">BRINDLEKILN</span>
      <span class="brand-mark"></span>
    </div>
    <p class="tagline">We deliver the<br>taste of barbecue<br>to the world.</p>
    <p class="intro">We have been manufacturing Smokers for over 50 years in Harlow Creek, OK. Brindlekiln is the leading authority in barbecue cooking, products and technology. We provide high-end products with exceptional satisfaction to our customers.</p>
    <div class="hero-photo" role="img" aria-label="Photo of golden roasted chickens on a smoker rack"></div>
    <div class="title-block">
      <p class="title-kicker">PRODUCT</p>
      <h1 class="title-main">CATALOG</h1>
    </div>
    <div class="product-frame first">
      <div class="product-shot" role="img" aria-label="Photo of a stainless steel commercial smoker cabinet on casters"></div>
    </div>
    <div class="product-frame second">
      <div class="product-shot" role="img" aria-label="Photo of a stainless steel rotisserie smoker with open door"></div>
    </div>
    <p class="contact">1-800-555-0147 | www.brindlekiln.com</p>
  </main>
</body>
</html>
```